New business card/stationary for a consulting company

I am looking for a clean and very professional looking business card for my consulting company as well as corresponding stationary. I am uploading our logo. I like simple and powerful for the feel. No graphics but I am open on everything else. Below is my contact information but would like the final to be in a version I can add my employees information into and print. Thank you.

Daniel Whitcombe
dan@ferncliffadvisory.com
2870 North 9th Avenue, Summit Floor, Elm Ridge, Illinois 60531
www.ferncliffadvisory.com

Industry/Entity Type

Consulting

Contact Information for Business Card

Daniel Whitcombe
dan@ferncliffadvisory.com
www.ferncliffadvisory.com

Font styles to use
Serif
Sans Serif

Requirements
Must have
• Our logo and the business card details.
Nice to have
• our website www.ferncliffadvisory.com

```html
<!DOCTYPE html>
<html lang="en">
<head>
<meta charset="utf-8">
<title>Ferncliff Advisory — Business Card</title>
<link rel="stylesheet" href="https://fonts.googleapis.com/css2?family=Montserrat:wght@400;600;700&family=Questrial&display=swap">
<style>
  :root {
    --brand-navy: #1f1f8a;
    --paper: #ffffff;
    --backdrop: #ececec;
    --ink: #2b2b2b;
  }
  * { box-sizing: border-box; margin: 0; padding: 0; }
  html, body {
    width: 1200px; height: 1000px; overflow: hidden;
    background: var(--backdrop);
  }
  .card {
    position: absolute; left: 100px; top: 214px;
    width: 1000px; height: 572px;
    background: var(--paper);
    box-shadow: 0 10px 30px rgba(0,0,0,0.12);
    font-family: "Montserrat", sans-serif;
    overflow: hidden;
  }
  .band { position: absolute; left: 0; width: 100%; background: var(--brand-navy); }
  .band--top { top: 0; height: 62px; }
  .band--bottom { bottom: 0; height: 74px; }

  .brand-mark {
    position: absolute; left: 560px; top: 128px;
    width: 136px; height: 72px;
    background: var(--brand-navy);
  }
  .brand-name {
    position: absolute; left: 320px; top: 208px;
    font-family: "Questrial", sans-serif;
    font-size: 40px; letter-spacing: 1px;
    color: var(--brand-navy); white-space: nowrap;
  }
  .divider {
    position: absolute; left: 60px; top: 262px;
    width: 640px; height: 2px; background: var(--brand-navy);
  }
  .contact-list { position: absolute; left: 34px; top: 282px; list-style: none; }
  .contact-list li {
    display: flex; align-items: center; gap: 12px;
    font-size: 21px; color: var(--ink); height: 36px;
  }
  .contact-list svg { width: 18px; height: 18px; flex: none; }

  .person {
    position: absolute; right: 50px; top: 312px; text-align: right;
  }
  .person__name { font-size: 34px; font-weight: 700; color: var(--brand-navy); line-height: 1.1; }
  .person__title { font-size: 20px; font-weight: 600; color: var(--brand-navy); margin-top: 4px; }
  .person__address { font-size: 20px; color: var(--ink); margin-top: 14px; line-height: 1.45; }
</style>
</head>
<body>
  <div class="card">
    <div class="band band--top"></div>

    <div class="brand-mark"></div>
    <div class="brand-name">FERNCLIFF ADVISORY</div>

    <div class="divider"></div>

    <ul class="contact-list">
      <li>
        <svg viewBox="0 0 18 18" aria-hidden="true"><rect x="1" y="4" width="16" height="11" fill="var(--brand-navy)"/><path d="M1 4 L9 10 L17 4" stroke="#fff" stroke-width="1.4" fill="none"/></svg>
        dan@ferncliffadvisory.com
      </li>
      <li>
        <svg viewBox="0 0 18 18" aria-hidden="true"><circle cx="9" cy="9" r="8" fill="var(--brand-navy)"/><path d="M1 9 H17 M9 1 V17 M3 5 H15 M3 13 H15" stroke="#fff" stroke-width="0.9" fill="none"/><ellipse cx="9" cy="9" rx="3.5" ry="8" stroke="#fff" stroke-width="0.9" fill="none"/></svg>
        www.ferncliffadvisory.com
      </li>
    </ul>

    <div class="person">
      <div class="person__name">Daniel Whitcombe</div>
      <div class="person__title">Founder / Principal</div>
      <div class="person__address">2870 North 9th Avenue, Summit Floor,<br>Elm Ridge, Illinois 60531</div>
    </div>

    <div class="band band--bottom"></div>
  </div>
</body>
</html>
```